Velk Partners Building Business Cards

We need a business card that reflects our business as "Solar Experts" in San Diego. Browse our website www.velkpartners.example our License needs to be displayed as "CSLB# 3867140" our phone number is (619) 555-0187

Save thousands on your electric bills and increase the value of your home while helping to protect the environment. Our solar installation experts will help you design the system that's right for you, using only the highest quality equipment that will look great and give you ideal performance. Our goal is to make you energy independent, and get your electric bill to 0.

Paul Osterby
(619) 555-0187
paul@velkpartners.example

Target Market(s)

Home owners in san diego looking for solar

Industry/Entity Type

Solar Energy

Contact Information for Business Card

Paul Osterby
(619) 555-0187
paul@velkpartners.example

Font styles to use
Other font styles liked:
• Use our logo font

Requirements
Must have
• License needs to be displayed as "CSLB# 3867140" our phone number is (619) 555-0187
Nice to have
• Real images of rooftop home solar in san diego
Should not have
• our business address

```html
<!DOCTYPE html>
<html lang="en">
<head>
<meta charset="utf-8">
<title>Velk Partners Building – Business Cards</title>
<link rel="stylesheet" href="https://fonts.googleapis.com/css2?family=Open+Sans:ital,wght@0,400;0,600;0,700;1,400&display=swap">
<style>
  :root {
    --backdrop: #3b3b3d;
    --card-white: #ffffff;
    --navy: #1a3d73;
    --gold: #f5ab00;
    --ink: #555a60;
    --rule: #c9ccd1;
  }
  * { box-sizing: border-box; margin: 0; padding: 0; }
  html, body {
    width: 1105px;
    height: 1200px;
    overflow: hidden;
  }
  body {
    background: var(--backdrop);
    font-family: "Open Sans", Arial, sans-serif;
    position: relative;
  }
  .card {
    position: absolute;
    left: 193px;
    width: 720px;
    height: 410px;
  }
  .card-front { top: 167px; background: var(--card-white); }
  .card-back  { top: 623px; background: var(--navy); }

  .brand-name {
    position: absolute;
    top: 100px;
    left: 0;
    width: 100%;
    text-align: center;
    font-weight: 700;
    font-size: 44px;
    letter-spacing: -0.5px;
    color: var(--navy);
  }

  .holder {
    position: absolute;
    right: 408px;
    top: 258px;
    text-align: right;
  }
  .holder-name {
    font-weight: 600;
    font-size: 25px;
    line-height: 32px;
    color: var(--navy);
  }
  .holder-title {
    font-size: 19px;
    line-height: 28px;
    color: var(--gold);
  }

  .divider {
    position: absolute;
    left: 344px;
    top: 225px;
    width: 1px;
    height: 122px;
    background: var(--rule);
  }

  .contact-list {
    position: absolute;
    left: 377px;
    top: 228px;
    list-style: none;
    font-size: 18px;
    color: var(--ink);
  }
  .contact-list li {
    display: flex;
    align-items: center;
    height: 28px;
  }
  .contact-list .license { margin-bottom: 5px; }
  .contact-icon {
    width: 16px;
    height: 16px;
    margin-right: 10px;
    flex: none;
  }

  .back-brand {
    position: absolute;
    top: 100px;
    left: 0;
    width: 100%;
    display: flex;
    flex-direction: column;
    align-items: center;
    gap: 26px;
  }
  .back-brand-dot {
    width: 96px;
    height: 96px;
    border-radius: 50%;
    background: var(--gold);
  }
  .back-brand-name {
    font-weight: 700;
    font-size: 34px;
    color: var(--card-white);
  }
  .back-url {
    position: absolute;
    top: 340px;
    left: 0;
    width: 100%;
    text-align: center;
    font-style: italic;
    font-size: 19px;
    letter-spacing: 4px;
    color: var(--card-white);
  }
</style>
</head>
<body>

<section class="card card-front">
  <div class="brand-name">Velk Partners Building</div>

  <div class="holder">
    <div class="holder-name">Paul Osterby</div>
    <div class="holder-title">CEO/Founder</div>
  </div>

  <div class="divider"></div>

  <ul class="contact-list">
    <li class="license">CSLB# 3867140</li>
    <li>
      <svg class="contact-icon" viewBox="0 0 16 16" aria-hidden="true">
        <path fill="#1a3d73" d="M3.2 1.2 5.6 1l1.3 3.4-1.6 1.3a9 9 0 0 0 5 5l1.3-1.6 3.4 1.3-.2 2.4c-.1.7-.7 1.2-1.4 1.2C6.6 15 1 9.4 1 2.6c0-.7.5-1.3 1.2-1.4z"/>
      </svg>
      (619) 555-0187
    </li>
    <li>
      <svg class="contact-icon" viewBox="0 0 16 16" aria-hidden="true">
        <rect x="1" y="3" width="14" height="10" fill="#1a3d73"/>
        <path d="M1.5 3.5 8 9l6.5-5.5" fill="none" stroke="#ffffff" stroke-width="1.3"/>
      </svg>
      paul@velkpartners.example
    </li>
    <li>
      <svg class="contact-icon" viewBox="0 0 16 16" aria-hidden="true">
        <circle cx="8" cy="8" r="7" fill="#1a3d73"/>
        <path d="M8 1v14M1 8h14M3 4.2c3 1.3 7 1.3 10 0M3 11.8c3-1.3 7-1.3 10 0" fill="none" stroke="#ffffff" stroke-width="0.9"/>
      </svg>
      www.velkpartners.example
    </li>
  </ul>
</section>

<section class="card card-back">
  <div class="back-brand">
    <div class="back-brand-dot"></div>
    <div class="back-brand-name">Velk Partners Building</div>
  </div>
  <div class="back-url">www.velkpartners.example</div>
</section>

</body>
</html>
```